CD Cover Design Project (Contemporary Country Album)

I am a country singer/songwriter in need of an album cover design (front/back/inside/CD) for my self-titled Nashville-recorded debut-EP release. My musical style is contemporary country/crossover so I want something that has the look and feel of current male country artist album covers (think Tavin Holloway, Wade Pemberford, Corey Vantrell, etc.).

I have attached several photos and a rough mix of the leading track. The CD template can be downloaded here:

http://www.plattervault.example/templates/ecowallets.asp# (4 Panel Eco-Wallet w/ Spine. Jewel Box Size (W139))

I will let you apply your vision (although I do think a more serious look, rather than the one pic where I am smiling, would be best suited for the cover). As mentioned, the album will be self-titled, as "Danny Kessler".

I really want the album design to show clearly who I am (may need to crop the pictures that are further away) as this will be going to publishing/record companies, etc. The track order for the back and inside is as follows:

1) Wildfire (Silver Porchlight style, song about meeting someone who is in a relationship) - this is the first track and is kind of the feel that should be reflected on at least the main cover

2) Small Moments Like These (uptempo song about a girl)

3) Driving Back Tonight (crossover, about a long distance relationship)

4) Harbor Lights (Henry Dowell style country song)

5) Toast (uptempo, fun party song)

Back Cover - There will need to be some room under the tracks for album credits (producer, etc.) which I will provide upon selecting a designer

Inside - The inside right cover will relist the album tracks and the smaller left panel will have some additional credits and website information (www.dannykessler.example)

I hope I have provided enough direction to get the ball rolling, and look forward to seeing your responses.
Updates

A cool, blue color scheme seems to be the direction I want to go, although not too dark.  It should be contemporary, cross-over (to pop) country feel (not classic, traditional country).

Target Market(s)

Contemporary country music fans

Industry/Entity Type

Singer

Requirements
Must have
• Danny Kessler clearly written as title on cover.

Track listing on back:

1) Wildfire
2) Small Moments Like These
3) Driving Back Tonight
4) Harbor Lights
5) Toast

Room for Producer/songwriting credits below - details TBD once designer is selected.

Inside Right and Left Panels can be worked on once designer is selected as well.

```html
<!DOCTYPE html>
<html lang="en">
<head>
<meta charset="utf-8">
<title>Danny Kessler – Eco-Wallet Layout</title>
<link href="https://fonts.googleapis.com/css2?family=Bebas+Neue&display=swap" rel="stylesheet">
<style>
  :root {
    --board: #a3aba3;
    --ink-dark: #0c1113;
    --teal-deep: #12282a;
    --teal-mid: #2f5a58;
    --steel: #3c4f5e;
    --portrait-light: #8d9a9a;
    --portrait-mid: #4f6470;
    --plaid: #2c4660;
    --gold: #e7bb1f;
    --white: #f2f2ee;
    --dieline: #c0399a;
    --fold: #b06aa0;
  }
  * { box-sizing: border-box; margin: 0; padding: 0; }
  html, body { width: 1200px; height: 684px; overflow: hidden; background: var(--board); }
  body { position: relative; font-family: "Bebas Neue", "Arial Narrow", sans-serif; color: var(--white); }

  .panel { position: absolute; overflow: hidden; }

  /* inner panel, printed upside down */
  .inner-panel { left: 778px; top: 25px; width: 339px; height: 307px;
    background: linear-gradient(180deg, #050708 0%, #151b1d 40%, #1b2426 62%, #0d1314 80%, #060809 100%); }
  .inner-panel .flip { position: absolute; inset: 0; transform: rotate(180deg); }
  .inner-tracks { position: absolute; left: 35px; top: 26px; list-style: none; font-size: 15px; line-height: 18.5px; letter-spacing: .4px; }
  .inner-credits { position: absolute; left: 35px; bottom: 20px; font-size: 8px; letter-spacing: .4px; }

  /* flap with thumb cut */
  .flap-panel { left: 80px; top: 333px; width: 336px; height: 305px; }
  .flap-photo { position: absolute; inset: 0;
    background: linear-gradient(180deg, #0d1416 0%, #1e2b2d 35%, #1a2527 68%, #263229 82%, #0b1010 100%); }
  .flap-figure { position: absolute; left: 100px; top: 52px; width: 92px; height: 250px;
    background: linear-gradient(180deg, #6f7c86 0%, #58687a 22%, #1f2428 45%, #2e3d55 62%, #1d2838 100%);
    border-radius: 40px 40px 6px 6px; }
  .thumb-cut { position: absolute; left: 0; top: 0; }

  /* back cover */
  .back-panel { left: 420px; top: 333px; width: 358px; height: 305px; }
  .back-photo { position: absolute; inset: 0;
    background: radial-gradient(ellipse 60% 55% at 55% 45%, #467572 0%, var(--teal-mid) 35%, var(--teal-deep) 78%, #0b1718 100%); }
  .artist { position: absolute; line-height: .95; }
  .artist .first { color: var(--gold); display: block; }
  .artist .last { color: var(--white); display: block; }
  .back-title { left: 32px; top: 30px; font-size: 37px; }

  .track-list { position: absolute; left: 32px; top: 144px; list-style: none; }
  .track-list li { font-size: 16px; line-height: 21.5px; white-space: nowrap; display: flex; align-items: flex-start; }
  .track-list .meta { display: inline-flex; flex-direction: column; margin-left: 2px; margin-top: 2px; line-height: 7px; }
  .track-list .credit { font-size: 6.5px; color: var(--white); }
  .track-list .time { font-size: 6.5px; color: var(--gold); }

  .back-footer { position: absolute; left: 32px; right: 26px; bottom: 8px; display: flex; justify-content: space-between; align-items: baseline; font-size: 7px; letter-spacing: .3px; }
  .back-footer .site { font-size: 8.5px; }

  .spine { position: absolute; left: 340px; top: 122px; writing-mode: vertical-rl; font-size: 9px; letter-spacing: .6px; }
  .spine .first { color: var(--gold); }

  /* front cover */
  .front-panel { left: 778px; top: 333px; width: 339px; height: 305px; }
  .front-photo { position: absolute; inset: 0;
    background: linear-gradient(100deg, #1b2f42 0%, var(--steel) 35%, #34495a 60%, #2a3d4d 100%); }
  .front-portrait { position: absolute; left: 88px; top: 0; width: 251px; height: 305px;
    background: linear-gradient(180deg, var(--portrait-light) 0%, var(--portrait-mid) 48%, var(--plaid) 70%, #1c3048 100%);
    border-radius: 120px 0 0 0; opacity: .9; }
  .front-title { left: 17px; top: 118px; }
  .front-title .first { font-size: 50px; }
  .front-title .last { font-size: 57px; }

  .marks { position: absolute; left: 0; top: 0; pointer-events: none; }
</style>
</head>
<body>

<section class="panel inner-panel">
  <div class="flip">
    <ol class="inner-tracks">
      <li>01. Wildfire</li>
      <li>02. Small Moments Like These</li>
      <li>03. Driving Back Tonight</li>
      <li>04. Harbor Lights</li>
      <li>05. Toast</li>
    </ol>
    <p class="inner-credits">CREDITS LOGOS ETC GO HERE......</p>
  </div>
</section>

<section class="panel flap-panel">
  <div class="flap-photo" role="img" aria-label="Dim brick warehouse interior"></div>
  <div class="flap-figure" role="img" aria-label="Full-length photo of the singer standing with an electric guitar"></div>
  <svg class="thumb-cut" width="120" height="305" viewBox="0 0 120 305" aria-hidden="true">
    <path d="M0 110 C0 120 6 122 16 122 H58 A33 33 0 0 1 58 188 H16 C6 188 0 190 0 200 Z" fill="var(--board)"/>
  </svg>
</section>

<section class="panel back-panel">
  <div class="back-photo" role="img" aria-label="Weathered teal metal wall texture"></div>
  <h2 class="artist back-title"><span class="first">DANNY</span><span class="last">KESSLER</span></h2>
  <ol class="track-list">
    <li>01. Wildfire<span class="meta"><span class="credit">PRODUCED BY SAM RIDLEY/ MUSIC BY DANNY KESSLER</span><span class="time">3:45</span></span></li>
    <li>02. Small Moments Like These<span class="meta"><span class="credit">PRODUCED BY SAM RIDLEY/ MUSIC BY DANNY KESSLER</span><span class="time">4:45</span></span></li>
    <li>03. Driving Back Tonight<span class="meta"><span class="credit">PRODUCED BY SAM RIDLEY/ MUSIC BY DANNY KESSLER</span><span class="time">4:33</span></span></li>
    <li>04. Harbor Lights<span class="meta"><span class="credit">PRODUCED BY SAM RIDLEY/ MUSIC BY DANNY KESSLER</span><span class="time">3:33</span></span></li>
    <li>05. Toast<span class="meta"><span class="credit">PRODUCED BY SAM RIDLEY/ MUSIC BY DANNY KESSLER</span><span class="time">3:09</span></span></li>
  </ol>
  <footer class="back-footer">
    <span>CREDITS ETC ..... PRODUCED BY SAM RIDLEY/ MUSIC BY DANNY KESSLER</span>
    <span class="site">WWW.DANNYKESSLER.EXAMPLE</span>
  </footer>
  <p class="spine"><span class="first">DANNY</span>&nbsp; KESSLER</p>
</section>

<section class="panel front-panel">
  <div class="front-photo" role="img" aria-label="Blue grunge wall background"></div>
  <div class="front-portrait" role="img" aria-label="Close portrait photo of the singer in a plaid shirt"></div>
  <h1 class="artist front-title"><span class="first">DANNY</span><span class="last">KESSLER</span></h1>
</section>

<svg class="marks" width="1200" height="684" viewBox="0 0 1200 684" aria-hidden="true">
  <line x1="80" y1="333" x2="778" y2="333" stroke="var(--dieline)" stroke-width="1"/>
  <line x1="778" y1="332" x2="1117" y2="332" stroke="var(--fold)" stroke-width="1" stroke-dasharray="2 2"/>
  <line x1="418" y1="334" x2="418" y2="638" stroke="var(--fold)" stroke-width="1" stroke-dasharray="2 2"/>
  <line x1="778" y1="334" x2="778" y2="638" stroke="var(--fold)" stroke-width="1" stroke-dasharray="2 2" opacity=".6"/>
</svg>

</body>
</html>
```